Sable Grove products by Voldrin. Beauty, skin care cosmetic products

We are an all natural and organic beauty product company looking for a logo an label design ideas. Our motto is to make products that are safe, natural, in harmony with the earth and that really work. Our products will contribute to the transition from the Old Earth to the Sable Grove (as the image of the two worlds suggests). The earths can be mixed in the label. The label example is a rough sketch.
Updates

The label needs to be 1 (one) inch high and 7 inch long.

Need extra days to review

Target Market(s)

Products made with natural and organic ingredients. Beauty and skin products

Requirements
Must have
• My project must be standing out. We want customers to be draw to he product on the shelf. Wow, this label is different? what is it? All natural? I must try it.
• Must be bold but not outrageous.
• The two earth can be placed on right and left side of the tree of life on the second attachment
Nice to have
• The two Earth can be in the back ground suggesting that this product takes us from chemically and artificially filled products to something new that is in harmony with nature and health.
Should not have
• Should not be boring. Ordinary, easy to forget and ignore patterns, lettering, logos.

```html
<!DOCTYPE html>
<html lang="en">
<head>
<meta charset="utf-8">
<title>Voldrin Under-Arm-Balm Label</title>
<link rel="stylesheet" href="https://fonts.googleapis.com/css2?family=Marcellus&display=swap">
<style>
  :root {
    --page: #ffffff;
    --night: #05070f;
    --deep-blue: #0d2a6b;
    --ocean: #2f5fb8;
    --sky: #6f8ee0;
    --violet: #7a6fd6;
    --ink-light: #e9e9ee;
    --ink-soft: #d6d8e2;
    --balm-yellow: #d9d21c;
    --rule: #c9c9cf;
  }
  * { margin: 0; padding: 0; box-sizing: border-box; }
  html, body {
    width: 1200px;
    height: 1019px;
    overflow: hidden;
    background: var(--page);
  }
  body {
    display: flex;
    align-items: center;
    justify-content: center;
    font-family: "Marcellus", serif;
  }
  .label {
    position: relative;
    width: 1100px;
    height: 460px;
    overflow: hidden;
  }
  .label-art {
    position: absolute;
    inset: 0;
    width: 100%;
    height: 100%;
  }
  .label-text {
    position: absolute;
    inset: 0;
    display: flex;
    flex-direction: column;
    align-items: center;
    justify-content: center;
    text-align: center;
    color: var(--ink-light);
    padding-top: 20px;
  }
  .maker {
    font-size: 30px;
    color: var(--ink-soft);
    letter-spacing: 0.5px;
    margin-bottom: 46px;
  }
  .claim {
    font-size: 37px;
    letter-spacing: 1px;
  }
  .claim-rule {
    width: 240px;
    height: 3px;
    margin: 12px 0 10px;
    background: linear-gradient(90deg, transparent, var(--rule) 20%, var(--rule) 80%, transparent);
  }
  .brand {
    font-size: 104px;
    line-height: 0.95;
    letter-spacing: 6px;
    color: var(--ink-light);
  }
  .product {
    font-size: 50px;
    line-height: 1.1;
    letter-spacing: 2px;
    color: var(--balm-yellow);
  }
  .free-from {
    margin-top: 8px;
    font-size: 22px;
    line-height: 1.25;
    color: var(--ink-soft);
    letter-spacing: 0.5px;
  }
</style>
</head>
<body>
  <section class="label">
    <svg class="label-art" viewBox="0 0 1100 460" preserveAspectRatio="none" role="img" aria-label="Background illustration of two earths, an old dark world on the left and a bright blue new world on the right">
      <defs>
        <linearGradient id="sky-band" x1="0" y1="0" x2="1" y2="0">
          <stop offset="0" stop-color="var(--night)"/>
          <stop offset="0.35" stop-color="#0a1430"/>
          <stop offset="0.6" stop-color="var(--deep-blue)"/>
          <stop offset="0.85" stop-color="var(--ocean)"/>
          <stop offset="1" stop-color="var(--sky)"/>
        </linearGradient>
        <radialGradient id="new-world" cx="0.78" cy="0.45" r="0.4">
          <stop offset="0" stop-color="var(--violet)" stop-opacity="0.85"/>
          <stop offset="1" stop-color="var(--violet)" stop-opacity="0"/>
        </radialGradient>
        <radialGradient id="old-world" cx="0.18" cy="0.6" r="0.35">
          <stop offset="0" stop-color="#1a2a22" stop-opacity="0.8"/>
          <stop offset="1" stop-color="#1a2a22" stop-opacity="0"/>
        </radialGradient>
      </defs>
      <rect width="1100" height="460" fill="url(#sky-band)"/>
      <rect width="1100" height="460" fill="url(#old-world)"/>
      <rect width="1100" height="460" fill="url(#new-world)"/>
    </svg>
    <div class="label-text">
      <p class="maker">Sable Grove Products by:</p>
      <p class="claim">100% NATURAL INGREDIENTS</p>
      <div class="claim-rule"></div>
      <h1 class="brand">VOLDRIN</h1>
      <p class="product">UNDER-ARM-BALM</p>
      <p class="free-from">No Aluminum, No Parabens,<br>No Phthalates</p>
    </div>
  </section>
</body>
</html>
```